Business Card Design for Training Business

Clear Path Coaching is a new business that delivers training and other services with a focus on topics related to mental health and wellbeing, for example, Wellmind Response Course, Resilience etc. We have a strong focus on evidence-based psychology and neuroscience. I have a logo which I will upload with the brief, so please consider colours that work well with the logo.
Target Market(s)
Adults, workplaces (particularly government and not-for-profits)
Industry/Entity Type
Business
Contact Information for Business Card
Head Strong TrainingSamantha SellwoodDirector0438 770 850sam@headstrongtraining.com.auwww.headstrongtraining.com.au

```html
<!DOCTYPE html>
<html lang="en">
<head>
<meta charset="utf-8">
<title>Clear Path Coaching – Business Card</title>
<link rel="stylesheet" href="https://fonts.googleapis.com/css2?family=Didact+Gothic&display=swap">
<style>
  :root {
    --page-bg: #d9dcdd;
    --card-top: #f4f6f6;
    --card-bottom: #e4e9ea;
    --ink-grey: #4a4a4c;
    --brand-teal: #2a9a95;
    --band-dark: #157874;
    --band-mid: #2fa59e;
    --band-light: #54bcb3;
    --arc-line: #3b302f;
    --band-text: #dff3f0;
  }
  * { box-sizing: border-box; margin: 0; padding: 0; }
  html, body {
    width: 1200px;
    height: 969px;
    overflow: hidden;
    background: var(--page-bg);
    font-family: "Didact Gothic", "Century Gothic", sans-serif;
  }
  .card {
    position: absolute;
    left: 100px;
    top: 202px;
    width: 1000px;
    height: 564px;
    border-radius: 30px;
    overflow: hidden;
    background: linear-gradient(180deg, var(--card-top), var(--card-bottom));
    box-shadow: 0 6px 24px rgba(0,0,0,0.12);
  }
  .card-band {
    position: absolute;
    inset: 0;
    width: 1000px;
    height: 564px;
  }
  .brand {
    position: absolute;
    left: 0;
    right: 0;
    top: 24px;
    text-align: center;
    color: var(--ink-grey);
  }
  .brand-mark {
    display: block;
    margin: 0 auto;
    width: 160px;
    height: 160px;
  }
  .brand-name {
    margin-top: 28px;
    font-size: 44px;
    letter-spacing: 5px;
    line-height: 1;
  }
  .brand-sub {
    margin-top: 14px;
    font-size: 24px;
    letter-spacing: 8px;
    line-height: 1;
  }
  .person {
    position: absolute;
    left: 0;
    right: 0;
    top: 382px;
    text-align: center;
    color: var(--band-text);
  }
  .person-name { font-size: 36px; line-height: 1; }
  .person-role { margin-top: 8px; font-size: 25px; line-height: 1; }
  .contact {
    position: absolute;
    left: 0;
    right: 0;
    text-align: center;
    color: var(--band-text);
    font-size: 23px;
    line-height: 1;
    display: flex;
    justify-content: center;
    align-items: center;
    gap: 36px;
  }
  .contact-row-main { top: 477px; }
  .contact-row-web { top: 512px; }
  .contact-item { display: inline-flex; align-items: center; gap: 10px; }
  .contact-icon { width: 22px; height: 22px; fill: var(--band-text); }
</style>
</head>
<body>
  <main class="card">
    <svg class="card-band" viewBox="0 0 1000 564" aria-hidden="true">
      <defs>
        <linearGradient id="bandFill" x1="0" y1="0" x2="1" y2="0">
          <stop offset="0" stop-color="var(--band-dark)"/>
          <stop offset="0.45" stop-color="var(--band-light)"/>
          <stop offset="1" stop-color="var(--band-dark)"/>
        </linearGradient>
      </defs>
      <path d="M0,462 Q500,232 1000,462 L1000,564 L0,564 Z" fill="url(#bandFill)"/>
      <path d="M0,452 Q500,222 1000,452" fill="none" stroke="var(--arc-line)" stroke-width="4"/>
    </svg>

    <header class="brand">
      <svg class="brand-mark" viewBox="0 0 160 160" aria-hidden="true">
        <circle cx="80" cy="80" r="76" fill="none" stroke="var(--brand-teal)" stroke-width="4"/>
      </svg>
      <p class="brand-name">CLEAR PATH</p>
      <p class="brand-sub">COACHING</p>
    </header>

    <section class="person">
      <p class="person-name">Rebecca Tanfield</p>
      <p class="person-role">Director</p>
    </section>

    <div class="contact contact-row-main">
      <span class="contact-item">
        <svg class="contact-icon" viewBox="0 0 24 24" aria-hidden="true"><path d="M6.6 10.8a15.1 15.1 0 0 0 6.6 6.6l2.2-2.2a1 1 0 0 1 1-.25 11.4 11.4 0 0 0 3.6.57 1 1 0 0 1 1 1V20a1 1 0 0 1-1 1A17 17 0 0 1 3 4a1 1 0 0 1 1-1h3.5a1 1 0 0 1 1 1c0 1.25.2 2.45.57 3.57a1 1 0 0 1-.25 1z"/></svg>
        0491 362 517
      </span>
      <span class="contact-item">
        <svg class="contact-icon" viewBox="0 0 24 24" aria-hidden="true"><path d="M3 5h18a1 1 0 0 1 1 1v12a1 1 0 0 1-1 1H3a1 1 0 0 1-1-1V6a1 1 0 0 1 1-1zm1 2.2V17h16V7.2l-8 5.3z M4.5 7h15L12 11.9z"/></svg>
        bec@clearpathcoaching.example.au
      </span>
    </div>
    <div class="contact contact-row-web">
      <span class="contact-item">
        <svg class="contact-icon" viewBox="0 0 24 24" aria-hidden="true"><path d="M12 2a10 10 0 1 0 0 20 10 10 0 0 0 0-20zm6.9 6h-3a15 15 0 0 0-1.3-3.9A8 8 0 0 1 18.9 8zM12 4c.9 1.2 1.6 2.5 2 4h-4c.4-1.5 1.1-2.8 2-4zM4.3 14a8 8 0 0 1 0-4h3.4a16 16 0 0 0 0 4zm.8 2h3a15 15 0 0 0 1.3 3.9A8 8 0 0 1 5.1 16zm3-8h-3a8 8 0 0 1 4.3-3.9A15 15 0 0 0 8.1 8zM12 20c-.9-1.2-1.6-2.5-2-4h4c-.4 1.5-1.1 2.8-2 4zm2.3-6H9.7a14 14 0 0 1 0-4h4.6a14 14 0 0 1 0 4zm.3 5.9A15 15 0 0 0 15.9 16h3a8 8 0 0 1-4.3 3.9zm1.7-5.9a16 16 0 0 0 0-4h3.4a8 8 0 0 1 0 4z"/></svg>
        www.clearpathcoaching.example.au
      </span>
    </div>
  </main>
</body>
</html>
```